BOLD & MINIMALIST DESIGN NEEDED

We want a very bold but minimalistic business card design that is impactful and utilizes both sides of the business card. Our current logo is included for your use.

We want bold fonts and good use of negative space. We don't want the logo to overpower the design.

Target Market(s)

Professionals who are building new commercial buildings.

Industry/Entity Type

Construction

Contact Information for Business Card

Name, Title, email, office phone, cell phone, website

Font styles to use
Serif
Sans Serif

Requirements
Must have
• Bold design!

```html
<!DOCTYPE html>
<html lang="en">
<head>
<meta charset="utf-8">
<title>Ridgeway Design + Build — Business Card</title>
<link rel="stylesheet" href="https://fonts.googleapis.com/css2?family=Montserrat:wght@400;500;800;900&display=swap">
<style>
  :root {
    --backdrop: #222222;
    --card-dark: #151515;
    --brand-green: #84c441;
    --brand-green-deep: #4f7f2e;
    --ink-light: #ffffff;
    --ink-soft: #e6e6e6;
  }
  * { box-sizing: border-box; margin: 0; padding: 0; }
  html, body {
    width: 1200px;
    height: 711px;
    overflow: hidden;
    background: var(--backdrop);
    font-family: "Montserrat", Arial, sans-serif;
  }
  .canvas {
    position: relative;
    width: 1200px;
    height: 711px;
    display: flex;
    justify-content: center;
    align-items: center;
    gap: 60px;
  }
  .card {
    width: 300px;
    height: 525px;
    border-radius: 22px;
    position: relative;
    overflow: hidden;
    box-shadow: 0 14px 30px rgba(0,0,0,0.55);
  }

  /* Reverse side */
  .card--back {
    background: var(--brand-green);
    display: flex;
    align-items: center;
    justify-content: center;
  }
  .back-mark {
    display: flex;
    align-items: center;
    gap: 10px;
    color: var(--brand-green-deep);
    font-weight: 900;
    font-size: 24px;
    letter-spacing: 1px;
    text-transform: uppercase;
  }
  .back-mark__square {
    width: 18px;
    height: 18px;
    background: var(--brand-green-deep);
  }

  /* Front side */
  .card--front {
    background: var(--card-dark);
    color: var(--ink-light);
    display: flex;
    flex-direction: column;
    align-items: center;
    padding: 70px 28px 0;
    text-align: center;
  }
  .brand {
    display: flex;
    align-items: center;
    gap: 9px;
  }
  .brand__square {
    width: 16px;
    height: 16px;
    background: var(--ink-light);
  }
  .brand__name {
    font-weight: 800;
    font-size: 22px;
    letter-spacing: 1px;
    text-transform: uppercase;
    color: var(--ink-light);
    line-height: 1.15;
  }
  .brand__tagline {
    font-weight: 800;
    font-size: 22px;
  }
  .person { margin-top: 62px; }
  .person__name {
    font-weight: 800;
    font-size: 25px;
    color: var(--brand-green);
    letter-spacing: 0.5px;
    text-transform: uppercase;
  }
  .person__title {
    font-weight: 400;
    font-size: 12px;
    letter-spacing: 0.8px;
    margin-top: 4px;
  }
  .icon-rule {
    margin-top: 22px;
    width: 100%;
    display: flex;
    align-items: center;
    gap: 8px;
  }
  .icon-rule__line {
    flex: 1;
    height: 1.5px;
    background: var(--brand-green);
  }
  .icon-rule__icons { display: flex; gap: 6px; }
  .contact-icon {
    width: 22px;
    height: 22px;
    border-radius: 6px;
    background: var(--brand-green);
    display: flex;
    align-items: center;
    justify-content: center;
  }
  .contact-list {
    list-style: none;
    margin-top: 20px;
    font-size: 12.5px;
    line-height: 1.75;
    color: var(--ink-soft);
  }
  .divider {
    margin-top: 18px;
    width: 150px;
    height: 1.5px;
    background: var(--brand-green);
  }
  .address {
    margin-top: 14px;
    font-style: normal;
    font-size: 12.5px;
    line-height: 1.6;
    color: var(--ink-soft);
  }
</style>
</head>
<body>
<main class="canvas">
  <section class="card card--back" aria-label="Card reverse">
    <div class="back-mark">
      <span class="back-mark__square"></span>
      <span>Ridgeway</span>
    </div>
  </section>

  <section class="card card--front" aria-label="Card front">
    <div class="brand">
      <span class="brand__square"></span>
      <span class="brand__name">Ridgeway<br><span class="brand__tagline">Design + Build</span></span>
    </div>

    <div class="person">
      <h1 class="person__name">Marcus Hale</h1>
      <p class="person__title">OWNER-CEO</p>
    </div>

    <div class="icon-rule">
      <span class="icon-rule__line"></span>
      <div class="icon-rule__icons">
        <span class="contact-icon" aria-label="Office phone">
          <svg width="13" height="13" viewBox="0 0 24 24"><path fill="#fff" d="M6.6 10.8a15 15 0 0 0 6.6 6.6l2.2-2.2a1 1 0 0 1 1-.25 11.4 11.4 0 0 0 3.6.57 1 1 0 0 1 1 1V20a1 1 0 0 1-1 1A17 17 0 0 1 3 4a1 1 0 0 1 1-1h3.5a1 1 0 0 1 1 1c0 1.25.2 2.45.57 3.57a1 1 0 0 1-.25 1z"/></svg>
        </span>
        <span class="contact-icon" aria-label="Mobile">
          <svg width="13" height="13" viewBox="0 0 24 24"><rect x="7" y="2" width="10" height="20" rx="2" fill="none" stroke="#fff" stroke-width="2"/><circle cx="12" cy="18" r="1.2" fill="#fff"/></svg>
        </span>
        <span class="contact-icon" aria-label="Email">
          <svg width="13" height="13" viewBox="0 0 24 24"><rect x="2" y="5" width="20" height="14" rx="1.5" fill="#fff"/><path d="M2 6l10 7 10-7" fill="none" stroke="#84c441" stroke-width="2"/></svg>
        </span>
        <span class="contact-icon" aria-label="Website">
          <svg width="13" height="13" viewBox="0 0 24 24"><circle cx="12" cy="12" r="9" fill="none" stroke="#fff" stroke-width="2"/><path d="M3 12h18M12 3c3 3 3 15 0 18M12 3c-3 3-3 15 0 18" fill="none" stroke="#fff" stroke-width="1.6"/></svg>
        </span>
      </div>
      <span class="icon-rule__line"></span>
    </div>

    <ul class="contact-list">
      <li>123 456 789</li>
      <li>123 456 789</li>
      <li>info@yourmail.com</li>
      <li>www.yourwebsite.com</li>
    </ul>

    <span class="divider"></span>

    <address class="address">
      Your address,<br>
      City State, Zip 1234
    </address>
  </section>
</main>
</body>
</html>
```